Timber Crest Construction Needs business card

Hey we are in need of business card designs. I have upload our logo as a guideline, but free feel to run with it or come up with something unique.
Pls have fun with it and be creative. the name says it all!
i will give some directions after i see a few entries..
Updates
Logo source file has been uploaded..
Hey because of the logo is so colourful already.
Can we have a few submissions with less colour.
Also we are looking for clever/hidden/descriptive business card.

```html
<!DOCTYPE html>
<html lang="en">
<head>
<meta charset="utf-8">
<title>Timber Crest Construction – Business Cards</title>
<link rel="stylesheet" href="https://fonts.googleapis.com/css2?family=Arimo:wght@400;700&display=swap">
<style>
  :root {
    --paper: #ffffff;
    --slate: #838386;
    --ink: #231f20;
    --text-dark: #1a1a1a;
    --text-grey: #808083;
    --edge: #7a7a7d;
  }
  * { margin: 0; padding: 0; box-sizing: border-box; }
  html, body { width: 1200px; height: 900px; overflow: hidden; background: var(--paper); }
  body { font-family: "Arimo", Arial, sans-serif; position: relative; }

  .card {
    position: absolute;
    width: 600px;
    height: 343px;
    border: 1px solid var(--edge);
    overflow: hidden;
  }
  .card--front { left: 0; }
  .card--back { left: 600px; background: var(--paper); }
  .set--slate .card { top: 0; }
  .set--ink .card { top: 557px; }
  .set--slate .card--front { background: var(--slate); }
  .set--ink .card--front { background: var(--ink); }

  .card__shape { position: absolute; left: -1px; top: -1px; width: 600px; height: 343px; }
  .card--front .card__shape polygon { fill: var(--paper); }
  .set--slate .card--back .card__shape polygon { fill: var(--slate); }
  .set--ink .card--back .card__shape polygon { fill: var(--ink); }

  .line {
    position: absolute;
    left: -1px;
    width: 600px;
    text-align: center;
    white-space: nowrap;
  }
  .proprietor { top: 36px; font-size: 17px; color: var(--text-dark); }
  .phone { top: 58px; font-size: 17px; color: var(--text-dark); }
  .wordmark {
    top: 186px;
    font-size: 29px;
    font-weight: 700;
    color: var(--text-grey);
    letter-spacing: 0.5px;
  }
  .address { top: 278px; font-size: 22px; color: var(--text-grey); }

  .detail { font-size: 26px; color: var(--paper); }
  .detail--features { top: 90px; }
  .detail--specialty { top: 172px; }
  .detail--contact { top: 250px; }
</style>
</head>
<body>

<section class="set set--slate">
  <article class="card card--front">
    <svg class="card__shape" viewBox="0 0 600 343" aria-hidden="true">
      <polygon points="172,34 429,34 429,78 515,78 515,168 573,168 573,274 515,274 515,310 86,310 86,274 28,274 28,168 86,168 86,78 172,78"/>
    </svg>
    <p class="line proprietor">Proprietor Name</p>
    <p class="line phone">0000000000</p>
    <p class="line wordmark">Timber Crest Construction</p>
    <p class="line address">Address</p>
  </article>
  <article class="card card--back">
    <svg class="card__shape" viewBox="0 0 600 343" aria-hidden="true">
      <polygon points="171,34 428,34 428,78 513,78 513,168 572,168 572,274 513,274 513,310 85,310 85,274 27,274 27,168 85,168 85,78 171,78"/>
    </svg>
    <p class="line detail detail--features">Work Features</p>
    <p class="line detail detail--specialty">Work specialty</p>
    <p class="line detail detail--contact">Contact Details</p>
  </article>
</section>

<section class="set set--ink">
  <article class="card card--front">
    <svg class="card__shape" viewBox="0 0 600 343" aria-hidden="true">
      <polygon points="172,34 429,34 429,78 515,78 515,168 573,168 573,274 515,274 515,310 86,310 86,274 28,274 28,168 86,168 86,78 172,78"/>
    </svg>
    <p class="line proprietor">Proprietor Name</p>
    <p class="line phone">0000000000</p>
    <p class="line wordmark">Timber Crest Construction</p>
    <p class="line address">Address</p>
  </article>
  <article class="card card--back">
    <svg class="card__shape" viewBox="0 0 600 343" aria-hidden="true">
      <polygon points="171,34 428,34 428,78 513,78 513,168 572,168 572,274 513,274 513,310 85,310 85,274 27,274 27,168 85,168 85,78 171,78"/>
    </svg>
    <p class="line detail detail--features">Work Features</p>
    <p class="line detail detail--specialty">Work specialty</p>
    <p class="line detail detail--contact">Contact Details</p>
  </article>
</section>

</body>
</html>
```